Electrician Business Card/ company logo/small business

New Business Cards and logo needed that will catch peoples eye and say we went that extra step. Attached is a design possibly to be incorporated, if u have your own great, lets see it!... This will be a small local business. thank you for all you do!
Halvern Electric
Ned Fosky Owner
Journeyman Electrician
phone 1.555.208.3471
email: KQLHalvernElectric@quellmail.net
call for free estimate!
Updates

Accepted and approved for cards

Target Market(s)

support small local business

Industry/Entity Type

Electrical,

Contact Information for Business Card

name, title,company/ logo, phone, email, free estimate

Other font styles liked:
• easy to read

Colors

Designer to choose colors to be used in the design.

Requirements
Must have
• eye catching everything! logo and halvern electric listed on business card/logo, incorp logo in the background of card
Nice to have
• lightening bolts in eyes or around the triangle? vertical, modern, any design that would be unique and stand out
Should not have
• pinks, reds, yellows,brown

```html
<!DOCTYPE html>
<html lang="en">
<head>
<meta charset="utf-8">
<title>Halvern Electric — Business Cards</title>
<link rel="stylesheet" href="https://fonts.googleapis.com/css2?family=Orbitron:wght@800&family=Arimo:wght@400&display=swap">
<style>
  :root {
    --backdrop: #121212;
    --card: #272729;
    --card-edge: #1a8fe0;
    --brand-blue: #168de2;
    --rule-blue: #1a8fe0;
    --text-light: #d8d8da;
    --mark-faint: #323235;
  }
  * { box-sizing: border-box; margin: 0; padding: 0; }
  html, body {
    width: 1200px; height: 820px; overflow: hidden;
    background: var(--backdrop);
  }
  .canvas {
    position: relative; width: 1200px; height: 820px;
    display: flex; align-items: center; justify-content: center; gap: 60px;
  }
  .card {
    position: relative; width: 520px; height: 298px;
    background: var(--card);
    border: 2px solid var(--card-edge);
    border-radius: 3px;
    box-shadow: 0 18px 40px rgba(0,0,0,.6);
    overflow: hidden;
  }
  .wordmark {
    font-family: "Orbitron", sans-serif; font-weight: 800;
    color: var(--brand-blue); text-transform: uppercase;
    letter-spacing: 1px; line-height: 1.05;
  }
  .brand-dot {
    width: 58px; height: 58px; border-radius: 50%;
    background: var(--brand-blue);
  }

  /* Front */
  .card-front .brand {
    position: absolute; top: 40px; left: 190px;
    display: flex; align-items: center; gap: 18px;
  }
  .card-front .wordmark { font-size: 24px; }
  .card-front .divider {
    position: absolute; left: 40px; right: 40px; top: 186px;
    height: 1px; background: var(--rule-blue);
  }
  .card-front .person {
    position: absolute; left: 40px; top: 132px;
  }
  .person-name {
    font-family: "Orbitron", sans-serif; font-weight: 800;
    font-size: 22px; color: var(--brand-blue); text-transform: uppercase;
    letter-spacing: 1px;
  }
  .person-title {
    font-family: "Arimo", sans-serif; font-size: 14px;
    color: var(--text-light); margin-top: 3px;
  }
  .contact-list {
    position: absolute; left: 40px; top: 204px; list-style: none;
    font-family: "Arimo", sans-serif; font-size: 14px; color: var(--text-light);
  }
  .contact-list li { display: flex; align-items: center; gap: 10px; margin-bottom: 7px; }
  .contact-list svg { width: 15px; height: 15px; fill: var(--brand-blue); flex: none; }

  /* Back */
  .card-back .faint-mark {
    position: absolute; left: 70px; top: 60px;
    width: 180px; height: 180px; border-radius: 50%;
    background: var(--mark-faint);
  }
  .card-back .wordmark {
    position: absolute; right: 36px; top: 124px; font-size: 26px;
  }
</style>
</head>
<body>
<main class="canvas">
  <section class="card card-front" aria-label="Business card front">
    <div class="brand">
      <div class="brand-dot"></div>
      <div class="wordmark">Halvern<br>Electric</div>
    </div>
    <div class="person">
      <h1 class="person-name">Ned Fosky</h1>
      <p class="person-title">Journeyman Electrician</p>
    </div>
    <div class="divider"></div>
    <ul class="contact-list">
      <li>
        <svg viewBox="0 0 24 24" aria-hidden="true"><path d="M6.6 10.8a15.1 15.1 0 0 0 6.6 6.6l2.2-2.2a1 1 0 0 1 1-.25 11.4 11.4 0 0 0 3.6.57 1 1 0 0 1 1 1V20a1 1 0 0 1-1 1A17 17 0 0 1 3 4a1 1 0 0 1 1-1h3.5a1 1 0 0 1 1 1c0 1.25.2 2.45.57 3.57a1 1 0 0 1-.25 1z"/></svg>
        <span>1.555.208.3471</span>
      </li>
      <li>
        <svg viewBox="0 0 24 24" aria-hidden="true"><path d="M2 5h20v14H2z M2 5l10 8 10-8" stroke="#272729" stroke-width="1.6"/></svg>
        <span>KQLHalvernElectric@quellmail.net</span>
      </li>
    </ul>
  </section>

  <section class="card card-back" aria-label="Business card back">
    <div class="faint-mark"></div>
    <div class="wordmark">Halvern<br>Electric</div>
  </section>
</main>
</body>
</html>
```